Market Research firm needs updated business cards with new logo

We need the logo to be included somewhere on the card (attached). We would also like the phrases "Independent, Objective, Comprehensive" and "Research You Can Trust" somewhere on the card. Front or back. Our colors are hex codes 6075a7, e48d25 and 5a5b5b. Though you are certainly not limited to those shades, whatever you produce should coordinate with them. I have also attached our favicon. Feel free to use it in your design, but please do not use it to replace the full logo.

Contact Information for Business Card

see project description

Font styles to use
Other font styles liked:
• Open Sans

Requirements
Must have
• the logo
• We use Open Sans font

```html
<!DOCTYPE html>
<html lang="en">
<head>
<meta charset="utf-8">
<title>Veritan Research — Business Card</title>
<link rel="stylesheet" href="https://fonts.googleapis.com/css2?family=Open+Sans:wght@400;600&family=Roboto:wght@300;700&family=EB+Garamond:wght@400&display=swap">
<style>
  :root {
    --brand-blue: #6075a7;
    --brand-blue-deep: #5567a0;
    --brand-orange: #e48d25;
    --brand-gray: #5a5b5b;
    --ink: #4a4b4b;
    --paper: #ffffff;
    --backdrop: #e4e4e4;
  }
  * { box-sizing: border-box; margin: 0; padding: 0; }
  html, body {
    width: 1200px; height: 900px; overflow: hidden;
    background: var(--backdrop);
  }
  .stage { position: relative; width: 1200px; height: 900px; }

  .card {
    position: absolute;
    width: 560px; height: 320px;
    background: var(--paper);
    border-radius: 18px;
    overflow: hidden;
    box-shadow: 0 6px 18px rgba(0,0,0,0.12);
  }
  .card--front { left: 80px; top: 80px; }
  .card--back  { left: 560px; top: 500px; }

  .band {
    position: absolute; left: 0; right: 0; bottom: 0;
    background: linear-gradient(90deg, var(--brand-blue-deep), var(--brand-blue) 55%, #7088bb);
  }
  .card--front .band { height: 42px; }
  .card--back .band { height: 22px; }

  .rule {
    position: absolute; height: 2px; background: var(--brand-blue-deep);
  }
  .rule--left  { left: 0; width: 130px; top: 212px; }
  .rule--right { right: 0; width: 130px; top: 100px; }

  .wordmark {
    font-family: "Open Sans", sans-serif;
    font-weight: 600;
    color: var(--brand-orange);
    white-space: nowrap;
    display: flex; align-items: center; gap: 8px;
  }
  .wordmark__dot {
    width: 0.55em; height: 0.55em; border-radius: 50%;
    background: var(--brand-orange);
  }
  .card--front .wordmark {
    position: absolute; left: 0; right: 0; top: 132px;
    justify-content: center; font-size: 36px;
  }
  .card--back .wordmark {
    position: absolute; right: 28px; top: 40px; font-size: 20px;
  }

  .front-url {
    position: absolute; left: 0; right: 0; top: 240px;
    text-align: center;
    font-family: "Roboto", sans-serif; font-weight: 700;
    font-size: 19px; color: var(--ink);
  }

  .identity { position: absolute; left: 44px; top: 96px; }
  .identity__name {
    font-family: "Roboto", sans-serif; font-weight: 700;
    font-size: 27px; color: var(--ink); letter-spacing: 0.3px;
  }
  .identity__title {
    font-family: "Roboto", sans-serif; font-weight: 300;
    font-size: 15px; color: var(--brand-gray); letter-spacing: 0.5px;
    margin-top: 2px;
  }
  .identity__underline {
    width: 96px; height: 3px; background: var(--brand-blue-deep); margin-top: 4px;
  }

  .contacts { position: absolute; left: 44px; top: 176px; list-style: none; }
  .contact { display: flex; align-items: center; gap: 14px; height: 42px; }
  .contact__icon {
    width: 30px; height: 30px; border-radius: 50%;
    background: var(--brand-blue-deep);
    display: flex; align-items: center; justify-content: center; flex: none;
  }
  .contact__text {
    font-family: "Open Sans", sans-serif; font-size: 13px;
    line-height: 1.3; color: var(--ink);
  }

  .tagline {
    position: absolute; right: 36px; top: 150px; width: 190px;
    text-align: center;
    font-family: "EB Garamond", serif; font-size: 16px; line-height: 1.3;
    color: #333;
  }
</style>
</head>
<body>
<main class="stage">

  <section class="card card--front" aria-label="Card front">
    <div class="rule rule--right"></div>
    <div class="rule rule--left"></div>
    <div class="wordmark"><span class="wordmark__dot"></span>Veritan Research</div>
    <p class="front-url">www.northbrook.com</p>
    <div class="band"></div>
  </section>

  <section class="card card--back" aria-label="Card back">
    <div class="wordmark"><span class="wordmark__dot"></span>Veritan Research</div>

    <div class="identity">
      <h1 class="identity__name">MARCUS HALLEY</h1>
      <p class="identity__title">SOLUTION MANAGER</p>
      <div class="identity__underline"></div>
    </div>

    <ul class="contacts">
      <li class="contact">
        <span class="contact__icon">
          <svg width="16" height="16" viewBox="0 0 24 24" aria-hidden="true"><path fill="#fff" d="M6.6 10.8a15.1 15.1 0 0 0 6.6 6.6l2.2-2.2a1 1 0 0 1 1-.25 11.4 11.4 0 0 0 3.6.57 1 1 0 0 1 1 1V20a1 1 0 0 1-1 1A17 17 0 0 1 3 4a1 1 0 0 1 1-1h3.5a1 1 0 0 1 1 1c0 1.25.2 2.45.57 3.6a1 1 0 0 1-.25 1z"/></svg>
        </span>
        <span class="contact__text">+8801555010203<br>+8801555010477</span>
      </li>
      <li class="contact">
        <span class="contact__icon">
          <svg width="16" height="16" viewBox="0 0 24 24" aria-hidden="true" fill="none" stroke="#fff" stroke-width="1.8"><circle cx="12" cy="12" r="9"/><ellipse cx="12" cy="12" rx="4" ry="9"/><path d="M3 12h18M5 7h14M5 17h14"/></svg>
        </span>
        <span class="contact__text">www.northbrookdesign.com<br>www.northbrook.com</span>
      </li>
      <li class="contact">
        <span class="contact__icon">
          <svg width="14" height="16" viewBox="0 0 24 24" aria-hidden="true"><path fill="#fff" d="M12 2a7 7 0 0 0-7 7c0 5.2 7 13 7 13s7-7.8 7-13a7 7 0 0 0-7-7zm0 9.5A2.5 2.5 0 1 1 12 6.5a2.5 2.5 0 0 1 0 5z"/></svg>
        </span>
        <span class="contact__text">East Riverpara, Kalinagar<br>Dhaka</span>
      </li>
    </ul>

    <p class="tagline">Independent, Objective<br>Comprehensive and<br>Research You Can Trust</p>

    <div class="band"></div>
  </section>

</main>
</body>
</html>
```